Oversized Postcard for Estate Planning & Probate 1st 2nd and 3rd prizes

Create a professional, fresh and polished oversized post card for law firm specializing in Estate Planning & Probate Law for High Net Worth Clients

Use any picture(s) of your choice (mine or ones you recommend), logo, headshot and company info

www.morvenashbylaw.com

Westbrook Office - 4800 Kestrel Avenue, Suite 900, Charlotte, NC 28210
Harlowe Office - 13470 Birch Court, Suite 400, Charlotte, NC 28277

Phone (704) 555-0187

Use this card for a Free Consultation

Target Market(s)

young and old families too; business owners

Industry/Entity Type

Law Firm

Font styles to use
Serif
Sans Serif

Requirements
Must have
• Use any picture(s) of your choice (mine or ones you recommend), logo, headshot and company info
• www.morvenashbylaw.com
• Westbrook Office - 4800 Kestrel Avenue, Suite 900, Charlotte, NC 28210
• Harlowe Office - 13470 Birch Court, Suite 400, Charlotte, NC 28277
• Phone (704) 555-0187
• Use this card for a Free Consultation
Nice to have
• great colors and great design; like graphics with depth /shading
Should not have
• don't use too many pics - keep it simple

```html
<!DOCTYPE html>
<html lang="en">
<head>
<meta charset="utf-8">
<title>Morven Ashby Law – Estate Planning Postcard</title>
<link rel="stylesheet" href="https://fonts.googleapis.com/css2?family=Bitter:wght@300;400;500&family=Montserrat:wght@300;400&display=swap">
<style>
  :root {
    --teal: #1a7ea6;
    --teal-mid: #0f6a8d;
    --teal-dark: #0b4d6a;
    --navy: #083b55;
    --band-grey: #d5d6d8;
    --ring-grey: #8a8d90;
    --text-grey: #8b8d90;
    --ink: #1d1d1d;
    --paper: #ffffff;
  }
  * { margin: 0; padding: 0; box-sizing: border-box; }
  html, body { width: 1200px; height: 771px; overflow: hidden; background: var(--paper); }
  .postcard {
    position: relative; width: 1200px; height: 771px; overflow: hidden;
    background: var(--paper); font-family: "Bitter", Georgia, serif;
  }
  .shapes { position: absolute; inset: 0; }
  .t { position: absolute; white-space: nowrap; line-height: 1; }

  .firm-block { position: absolute; left: 718px; top: 34px; width: 286px; text-align: right;
    border-top: 2px dotted var(--teal); border-bottom: 2px dotted var(--teal); padding: 12px 0 10px; }
  .firm-name { font-size: 22px; font-weight: 500; color: var(--teal); line-height: 1.1; }
  .firm-contact { font-size: 18.5px; font-weight: 300; color: var(--text-grey); line-height: 1.35; margin-top: 3px; }

  .attorney { position: absolute; left: 376px; top: 146px; width: 278px; text-align: center; }
  .attorney-name { font-size: 29px; font-weight: 400; color: var(--teal); line-height: 1; }
  .attorney-creds { font-size: 16px; font-weight: 300; color: var(--text-grey); margin-top: 9px;
    padding-bottom: 7px; border-bottom: 2px dotted var(--teal); }
  .attorney-cert { font-size: 16px; color: var(--ink); line-height: 1.25; margin-top: 8px; }

  .cta-lead { left: 330px; top: 318px; font-size: 19px; font-weight: 500; color: var(--teal); }
  .cta-call { left: 320px; top: 365px; font-family: "Montserrat", Arial, sans-serif; font-size: 19px; font-weight: 300; color: var(--text-grey); }
  .cta-phone { left: 360px; top: 346px; font-family: "Montserrat", Arial, sans-serif; font-size: 40px; font-weight: 300; color: var(--text-grey); letter-spacing: 0.5px; }

  .brand-name { left: 46px; width: 310px; top: 556px; text-align: center; font-size: 38px; font-weight: 400; color: var(--teal); }
  .brand-suffix { left: 46px; width: 310px; top: 609px; text-align: center; font-size: 17px; color: var(--ink); letter-spacing: 1px; }

  .office-title { left: 474px; font-size: 21px; color: var(--teal); padding-bottom: 4px; border-bottom: 2px dotted var(--teal); }
  .office-address { left: 474px; font-size: 17px; color: var(--text-grey); line-height: 1.25; }

  .tagline { left: 22px; color: #fff; font-size: 19.5px; line-height: 1.22; }
</style>
</head>
<body>
<main class="postcard">
  <svg class="shapes" width="1200" height="771" viewBox="0 0 1200 771" aria-hidden="true">
    <!-- accent stripes under the credentials -->
    <polygon points="320,272 420,272 440,297 320,297" fill="var(--teal)"/>
    <polygon points="416,272 555,272 575,297 436,297" fill="var(--teal-mid)"/>
    <polygon points="551,272 686,272 708,297 571,297" fill="var(--teal-dark)"/>
    <!-- appointment band -->
    <polygon points="0,302 708,302 614,395 0,395" fill="var(--band-grey)"/>
    <!-- dividers -->
    <line x1="454" y1="419" x2="454" y2="668" stroke="#9a9c9f" stroke-width="2"/>
    <line x1="770" y1="222" x2="770" y2="613" stroke="#2a2a2a" stroke-width="2"/>
    <!-- brand mark circle -->
    <circle cx="202" cy="472" r="52" fill="var(--teal-dark)" stroke="#1d1d1d" stroke-width="3"/>
    <!-- brand rules -->
    <line x1="46" y1="535" x2="356" y2="535" stroke="#1d1d1d" stroke-width="2"/>
    <line x1="46" y1="618" x2="144" y2="618" stroke="#1d1d1d" stroke-width="2"/>
    <line x1="258" y1="618" x2="356" y2="618" stroke="#1d1d1d" stroke-width="2"/>
    <!-- footer bands -->
    <polygon points="0,658 270,658 330,718 0,718" fill="var(--teal-mid)"/>
    <polygon points="0,718 366,718 418,771 0,771" fill="var(--navy)"/>
    <polygon points="690,746 868,746 893,771 715,771" fill="var(--navy)"/>
    <polygon points="864,746 1045,746 1070,771 889,771" fill="var(--teal-dark)"/>
    <polygon points="1041,746 1200,746 1200,771 1066,771" fill="var(--teal)"/>
    <!-- headshot frame -->
    <circle cx="196" cy="196" r="158" fill="#fff" stroke="var(--ring-grey)" stroke-width="5"/>
  </svg>

  <svg class="shapes" width="1200" height="771" viewBox="0 0 1200 771" role="img" aria-label="Headshot portrait of attorney Morven L. Ashby">
    <defs>
      <radialGradient id="portraitTone" cx="50%" cy="45%" r="60%">
        <stop offset="0%" stop-color="#d9b68a"/>
        <stop offset="55%" stop-color="#8a6d4f"/>
        <stop offset="100%" stop-color="#1c1a19"/>
      </radialGradient>
    </defs>
    <circle cx="196" cy="196" r="149" fill="url(#portraitTone)"/>
  </svg>

  <div class="firm-block">
    <div class="firm-name">Morven Ashby Law, PLLC</div>
    <div class="firm-contact">morven@morvenashbylaw.com<br>www.morvenashbylaw.com</div>
  </div>

  <div class="attorney">
    <div class="attorney-name">Morven L. Ashby</div>
    <div class="attorney-creds">Attorney, CPA, CFM, CMA, MAc.</div>
    <div class="attorney-cert">Board Certified Specialist in<br>Estate Planning and Probate Law</div>
  </div>

  <div class="t cta-lead">To schedule an appointment</div>
  <div class="t cta-call">call</div>
  <div class="t cta-phone">704-555-0187</div>

  <div class="t brand-name">Morven Ashby</div>
  <div class="t brand-suffix">LAW PLLC</div>

  <div class="t office-title" style="top:452px">Westbrook Office</div>
  <div class="t office-address" style="top:486px">4800 Kestrel Avenue, Suite 900<br>Charlotte, NC 28210</div>
  <div class="t office-title" style="top:571px">Harlowe Office</div>
  <div class="t office-address" style="top:605px">13470 Birch Court, Suite 400<br>Charlotte, NC 28277</div>

  <div class="t tagline" style="top:668px">Charlotte Estate Planning<br>&amp; Probate Attorneys</div>
  <div class="t tagline" style="top:730px">Elise Brantley Harwood Attorney</div>
</main>
</body>
</html>
```